National online rug retailer needs a home page design

See the FloorNest logo and create a home page design around that color theme. Details are spelled out in word document uploaded below.

Apparently this website did not take my attachement showing the logo and basic requirements.  If you would send me your email address, I will send you the attachment directly.
Best regards,
Tom Vance
tvance@mrdcorp.example

Target Market(s)

The target market is home owners 25 to 75 years old with combined incomes over $100,000 per year.

Industry/Entity Type

Online

Requirements
Must have
• Lots of white space with black letters and creative use of red and possibly one other color. Would like a compelling call to action button.

```html
<!DOCTYPE html>
<html lang="en">
<head>
<meta charset="utf-8">
<title>FloorNest.com – Home</title>
<link href="https://fonts.googleapis.com/css2?family=Roboto:wght@300;400;500;700&display=swap" rel="stylesheet">
<style>
:root{
  --red:#e3141b;
  --red-dark:#c40f15;
  --ink:#111;
  --text:#444;
  --muted:#666;
  --line:#ddd;
  --dark:#3d3d3f;
  --footer:#efefef;
  --white:#fff;
}
*{margin:0;padding:0;box-sizing:border-box}
html,body{width:867px;height:1200px;overflow:hidden;background:var(--white)}
body{font-family:"Roboto",Arial,sans-serif;color:var(--ink);position:relative}
.abs{position:absolute}
a{color:inherit;text-decoration:none}

/* header */
.brand{left:92px;top:20px}
.brand-name{font-size:36px;font-weight:500;color:var(--red);letter-spacing:-1px;line-height:40px}
.brand-tag{font-size:9px;color:var(--muted);margin-left:66px;margin-top:2px}
.search{left:353px;top:38px;width:160px;height:26px;border:1px solid #ccc;font-size:8px;color:#999;padding:8px 7px}
.search-btn{left:517px;top:38px;width:25px;height:26px;background:#5b5b5d}
.util{right:93px;text-align:right;font-size:9px;color:var(--muted)}
.util b{color:var(--ink);font-weight:500}
.util .sep{margin:0 3px}
.phone{top:40px;font-size:12px;color:var(--muted)}
.phone span{color:var(--red);font-weight:500}

/* nav */
.nav{left:92px;top:98px;width:684px;height:35px;background:var(--red);border:2px solid var(--red-dark);
  display:flex;align-items:center;justify-content:space-between;padding:0 9px 0 14px;
  color:var(--white);font-size:9.5px;font-weight:700;letter-spacing:.2px}
.nav .bar{font-weight:400;opacity:.9}

/* hero */
.hero{left:92px;top:145px;width:684px;height:210px;border:1px solid #ccc;padding:4px}
.hero-photo{width:100%;height:100%;background:linear-gradient(90deg,#cfd3d6 0%,#eceeef 35%,#dfe2e4 60%,#e9ebec 100%)}
.hero-copy{left:516px;top:172px;color:#444;font-weight:300}
.save{font-size:27px;color:var(--red);line-height:1}
.save big{font-size:62px;font-weight:300;vertical-align:-2px}
.ship{font-size:24px;color:var(--red);line-height:1.2;margin-top:-4px}
.values{font-size:22px;line-height:1.15;margin-top:3px;color:#555;letter-spacing:.5px}

/* browse */
.browse{left:92px;top:374px;width:82px;height:25px;background:var(--red);color:var(--white);font-size:11px;font-weight:500;text-align:center;line-height:25px}
.browse:after{content:"";position:absolute;right:-6px;top:8px;border-left:6px solid var(--red);border-top:5px solid transparent;border-bottom:5px solid transparent}
.filter{top:374px;height:25px;border:1px solid #bbb;font-size:8.5px;line-height:23px;padding:0 8px;display:flex;justify-content:space-between}
.go{left:733px;top:374px;width:43px;height:25px;background:var(--red);color:var(--white);font-size:11px;text-align:center;line-height:25px;border:1px solid var(--red-dark)}

/* section titles */
.section-title{font-size:12px;font-weight:500;color:#333}
.rule{height:1px;background:var(--line)}

/* collections */
.coll{top:454px;width:218px}
.coll-img{height:98px}
.coll h3{font-size:11px;font-weight:500;margin-top:15px}
.coll h3 .chev{color:var(--red);margin-left:12px}
.coll p{font-size:9px;line-height:12.2px;color:var(--text);margin-top:12px}
.coll .more{display:block;font-size:10px;font-weight:500;margin-top:14px}
.coll .more span{color:var(--red);margin-left:10px;font-weight:700}

/* products */
.arrows{left:745px;top:697px}
.product{top:746px;width:142px}
.product-img{height:105px}
.sale{position:absolute;right:-10px;top:-3px;width:35px;height:35px;border-radius:50%;background:var(--red);color:var(--white);font-size:8.5px;text-align:center;line-height:35px}
.pline{margin-top:10px;height:1px;background:var(--line);position:relative}
.pline:before{content:"";position:absolute;left:10px;top:0;width:16px;height:2px;background:var(--red)}
.pname{font-size:8.5px;color:#333;margin-top:16px}
.price{font-size:10px;color:#333;margin-top:4px}
.price span{color:var(--red)}
.cart{position:absolute;right:0;top:134px;width:25px;height:24px;background:#4a4a4c;border-radius:2px}

/* footer */
.footer{left:86px;top:939px;width:694px;height:261px;background:var(--footer)}
.fcol{top:966px}
.fcol h4{font-size:10px;font-weight:500;color:#333}
.fcol ul{list-style:none;margin-top:25px}
.fcol li{font-size:8.5px;color:#333;line-height:13.7px}
.card{top:1004px;width:22px;height:15px;border-radius:2px}
.badge{top:1041px;height:32px}
.copyright{left:86px;top:1162px;width:694px;height:38px;background:var(--dark);color:#bbb;font-size:8.5px;text-align:center;line-height:38px}
</style>
</head>
<body>

<header>
  <div class="abs brand">
    <div class="brand-name">FloorNest.com</div>
    <div class="brand-tag">for domestic and heirloom values</div>
  </div>
  <div class="abs search">Enter a keyword or item</div>
  <div class="abs search-btn">
    <svg width="25" height="26" viewBox="0 0 25 26"><circle cx="11.5" cy="12" r="4.2" fill="none" stroke="#fff" stroke-width="1.5"/><line x1="14.5" y1="15" x2="18" y2="18.5" stroke="#fff" stroke-width="1.6"/></svg>
  </div>
  <div class="abs util" style="top:24px">Items (0) <b>Total $0.00</b> View Cart<span class="sep">|</span>Checkout</div>
  <div class="abs util phone">Order Toll-Free : <span>1-800-555-0142</span></div>
  <div class="abs util" style="top:60px">My Account<span class="sep">|</span>Sign &nbsp;
    <svg width="9" height="9" viewBox="0 0 9 9"><path d="M1 1h4v4L2 7z" fill="#333"/><path d="M4 3h4v4H6L5 8z" fill="#333"/></svg> Live Chat &nbsp;
    <svg width="9" height="9" viewBox="0 0 9 9"><circle cx="4.5" cy="2.5" r="2" fill="#333"/><path d="M0.5 9a4 3.5 0 0 1 8 0z" fill="#333"/></svg> Online</div>
</header>

<nav class="abs nav">
  <a>HOME</a><span class="bar">I</span>
  <a>SELECTION GUIDES</a><span class="bar">I</span>
  <a>RUG CARE</a><span class="bar">I</span>
  <a>FAQ</a><span class="bar">I</span>
  <a>RETURN POLICY</a><span class="bar">I</span>
  <a>FREE SHIPPING</a><span class="bar">I</span>
  <a>CLEARANCE RUGS</a>
</nav>

<section class="abs hero">
  <div class="hero-photo" role="img" aria-label="Bright room with tall windows and a striped runner rug on a white floor"></div>
</section>
<div class="abs hero-copy">
  <div class="save">SAVE <big>75%</big></div>
  <div class="ship">+ FREE SHIPPING</div>
  <div class="values">FOR DOMESTIC AND<br>HERILOOM VALUES</div>
</div>

<div class="abs browse">BROWSE</div>
<div class="abs filter" style="left:190px;width:81px">Rug Theme<span>+</span></div>
<div class="abs filter" style="left:277px;width:81px">Color Way<span>+</span></div>
<div class="abs filter" style="left:364px;width:81px">Size &amp; Shape<span>+</span></div>
<div class="abs filter" style="left:452px;width:81px">Fiber Content<span>+</span></div>
<div class="abs filter" style="left:539px;width:81px">Mfgr.brand<span>+</span></div>
<div class="abs filter" style="left:626px;width:96px">Collection &amp; Price<span>+</span></div>
<div class="abs go">GO</div>

<h2 class="abs section-title" style="left:92px;top:427px">YOU MAY ALSO LIKE</h2>
<div class="abs rule" style="left:232px;top:433px;width:540px"></div>

<article class="abs coll" style="left:92px">
  <div class="coll-img" role="img" aria-label="Purple geometric rug close-up" style="background:linear-gradient(135deg,#7a4fa8,#9b6cc4 60%,#6c3f98)"></div>
  <h3>Home Classic Collection<span class="chev">&gt;</span></h3>
  <p>Lorem Ipsum is simply dummy text of the printing and typesetting industry. Lorem Ipsum has been the industry's standard dummy text ever since the 1500s, when an unknown printer took.</p>
  <a class="more">Read More<span>&gt;&gt;</span></a>
</article>
<article class="abs coll" style="left:324px">
  <div class="coll-img" role="img" aria-label="Rug with large red and gold rose pattern on wood floor" style="background:linear-gradient(135deg,#8a5a2a,#7a1a14 50%,#b0652a)"></div>
  <h3>Home Rugs Collection<span class="chev">&gt;</span></h3>
  <p>Lorem Ipsum is simply dummy text of the printing and typesetting industry. Lorem Ipsum has been the industry's standard dummy text ever since the 1500s, when an unknown printer took.</p>
  <a class="more">Read More<span>&gt;&gt;</span></a>
</article>
<article class="abs coll" style="left:556px">
  <div class="coll-img" role="img" aria-label="Modern living room with black chair and grey patterned rug" style="background:linear-gradient(180deg,#d9dcdd,#b8bbbc 60%,#9ea1a2)"></div>
  <h3>Home Casual Collection<span class="chev">&gt;</span></h3>
  <p>Lorem Ipsum is simply dummy text of the printing and typesetting industry. Lorem Ipsum has been the industry's standard dummy text ever since the 1500s, when an unknown printer took.</p>
  <a class="more">Read More<span>&gt;&gt;</span></a>
</article>

<div class="abs rule" style="left:86px;top:689px;width:694px"></div>
<h2 class="abs section-title" style="left:92px;top:697px">NEW PRODUCTS</h2>
<div class="abs arrows">
  <svg width="24" height="14" viewBox="0 0 24 14"><path d="M9 1L1 7l8 6z" fill="#444"/><path d="M15 1l8 6-8 6z" fill="#444"/></svg>
</div>
<div class="abs rule" style="left:86px;top:722px;width:694px"></div>

<div class="abs product" style="left:94px">
  <div class="product-img" role="img" aria-label="Dark rug with colourful ring pattern" style="background:linear-gradient(135deg,#3a2a22,#5a3a28 50%,#2e2420)"></div>
  <div class="sale">Sale</div><div class="pline"></div>
  <div class="pname">Lorem ipsum dolor sit</div>
  <div class="price">$219.00 <span>$182.00</span></div>
  <div class="cart"><svg width="25" height="24" viewBox="0 0 25 24"><path d="M7 8h2l1.5 6h6l1.5-4.5H10" fill="none" stroke="#fff" stroke-width="1.3"/><circle cx="11" cy="16.5" r="1" fill="#fff"/><circle cx="16" cy="16.5" r="1" fill="#fff"/></svg></div>
</div>
<div class="abs product" style="left:272px">
  <div class="product-img" role="img" aria-label="Grey patterned rug in modern living room" style="background:linear-gradient(180deg,#dcdfe0,#b5b8b9)"></div>
  <div class="sale">Sale</div><div class="pline"></div>
  <div class="pname">Lorem ipsum dolor sit</div>
  <div class="price">$219.00 <span>$182.00</span></div>
  <div class="cart"><svg width="25" height="24" viewBox="0 0 25 24"><path d="M7 8h2l1.5 6h6l1.5-4.5H10" fill="none" stroke="#fff" stroke-width="1.3"/><circle cx="11" cy="16.5" r="1" fill="#fff"/><circle cx="16" cy="16.5" r="1" fill="#fff"/></svg></div>
</div>
<div class="abs product" style="left:451px">
  <div class="product-img" role="img" aria-label="Red, white and grey shag rug before a sofa" style="background:linear-gradient(180deg,#c9c9c9,#b04848 45%,#d8d6d4)"></div>
  <div class="sale">Sale</div><div class="pline"></div>
  <div class="pname">Lorem ipsum dolor sit</div>
  <div class="price">$219.00 <span>$182.00</span></div>
  <div class="cart"><svg width="25" height="24" viewBox="0 0 25 24"><path d="M7 8h2l1.5 6h6l1.5-4.5H10" fill="none" stroke="#fff" stroke-width="1.3"/><circle cx="11" cy="16.5" r="1" fill="#fff"/><circle cx="16" cy="16.5" r="1" fill="#fff"/></svg></div>
</div>
<div class="abs product" style="left:629px">
  <div class="product-img" role="img" aria-label="Deep red rug on light wood floor" style="background:linear-gradient(180deg,#e2d6c4,#a62018 40%,#c89a6a)"></div>
  <div class="sale">Sale</div><div class="pline"></div>
  <div class="pname">Lorem ipsum dolor sit</div>
  <div class="price">$219.00 <span>$182.00</span></div>
  <div class="cart"><svg width="25" height="24" viewBox="0 0 25 24"><path d="M7 8h2l1.5 6h6l1.5-4.5H10" fill="none" stroke="#fff" stroke-width="1.3"/><circle cx="11" cy="16.5" r="1" fill="#fff"/><circle cx="16" cy="16.5" r="1" fill="#fff"/></svg></div>
</div>

<footer>
  <div class="abs footer"></div>
  <div class="abs rule" style="left:106px;top:982px;width:640px;background:#ccc"></div>
  <div class="abs fcol" style="left:106px"><h4>Customer Services</h4>
    <ul><li>Shipping</li><li>Return Policy</li><li>Privacy Policy</li><li>Ordering &amp; Delivery</li><li>Checklist</li><li>Terms of Use</li><li>Terms of Sale</li><li>Contact Us</li><li>Environmental Policy</li></ul></div>
  <div class="abs fcol" style="left:246px"><h4>Resources</h4>
    <ul><li>Product Articles</li><li>Learning Center</li><li>Help</li><li>Refer A Friend</li><li>FloorNest Blog</li><li>Room Scene Viewer</li><li>Site Map</li><li>FAQ</li><li>Customer Testimonials</li><li>Photo Gallery</li></ul></div>
  <div class="abs fcol" style="left:377px"><h4>Corporate Info</h4>
    <ul><li>About FloorNest.com</li><li>Careers</li><li>Affiliates</li></ul></div>
  <div class="abs fcol" style="left:518px"><h4>Payments &amp; Security</h4></div>

  <div class="abs card" style="left:520px;background:#1b3a8a"></div>
  <div class="abs card" style="left:546px;background:#e8e8e8;border:1px solid #bbb"></div>
  <div class="abs card" style="left:572px;background:#2a4aa0"></div>
  <div class="abs card" style="left:598px;background:#3a8ac8"></div>
  <div class="abs card" style="left:624px;background:#f3b32a"></div>
  <div class="abs card" style="left:656px;width:92px;height:22px;top:1000px;background:#cfd8e6"></div>

  <div class="abs badge" style="left:516px;width:32px;border-radius:50%;background:#d4b43a"></div>
  <div class="abs badge" style="left:558px;width:34px;border-radius:50%;background:#e8c83a"></div>
  <div class="abs badge" style="left:594px;width:46px;height:18px;top:1049px;background:#d8d8d8;border:1px solid #999"></div>
  <div class="abs badge" style="left:643px;width:44px;height:22px;top:1047px;background:#2f5ea8"></div>
  <div class="abs badge" style="left:690px;width:54px;height:24px;top:1046px;background:#dcdcdc;border:1px solid #999"></div>

  <div class="abs copyright">© Copyrights 2013 &nbsp;FloorNest. All rights Reserved</div>
</footer>

</body>
</html>
```